Catering Menu Package

I currently have a complete menu package, which we have redesigned as far as content, now I need to it put together in a catalog type format. It is essentially 10-12 pages in length, and will be sent for print production. Upon receiving a final edit
Updates

I have added an example gif to the project.

I did this free hand this basically what I am looking for. please change text and type to whatever you think would look best. This is a total rough design so, feel free to change any and everything. The text for the page is on the word documents. If you need more images let me know I am in the process of getting as many images uploaded for your use.

Project Deadline Extended
Reason: I figured we got a late jump with questions, so i am extending a few days .

Target Market(s)

The target market is business who wish to have catered luncheons, breakfasts , meetings

Industry/Entity Type

Catering

Requirements
Must have
• I have attached a copy of the text that what we want in the package, our logo, and i have also attached a catering package of another company to give you an idea what the finished product will be
Should not have
• It should not look identical to the example catering packages, these are for some inspiration we want our own design with the same type of look and feel

```html
<!DOCTYPE html>
<html lang="en">
<head>
<meta charset="utf-8">
<title>Hearty Breakfast — Catering Menu</title>
<link rel="stylesheet" href="https://fonts.googleapis.com/css2?family=UnifrakturCook:wght@700&family=Great+Vibes&family=Gabriela&family=Sorts+Mill+Goudy&display=swap">
<style>
  :root {
    --paper: #ece6da;
    --paper-light: #f3eee5;
    --ink: #141010;
    --rule-soft: #9a958c;
    --photo-red: #b8321f;
    --photo-cream: #e9c98f;
    --photo-deep: #7c1d12;
  }
  html, body {
    margin: 0;
    padding: 0;
    overflow: hidden;
    background: #ffffff;
  }
  .menu-page {
    position: relative;
    width: 1200px;
    height: 928px;
    overflow: hidden;
    background: var(--paper);
    color: var(--ink);
  }
  .food-photo {
    position: absolute;
    left: 0;
    top: 0;
    width: 507px;
    height: 928px;
    background:
      radial-gradient(ellipse at 30% 20%, var(--photo-cream) 0%, transparent 45%),
      radial-gradient(ellipse at 70% 55%, var(--photo-cream) 0%, transparent 40%),
      radial-gradient(ellipse at 40% 85%, #f1dcb4 0%, transparent 45%),
      linear-gradient(160deg, var(--photo-red) 0%, var(--photo-deep) 50%, var(--photo-red) 100%);
  }
  .content {
    position: absolute;
    left: 507px;
    top: 0;
    width: 693px;
    height: 928px;
    background: linear-gradient(180deg, var(--paper-light), var(--paper));
  }
  .page-title {
    position: absolute;
    left: 8px;
    top: 14px;
    margin: 0;
    font-family: "UnifrakturCook", serif;
    font-weight: 700;
    font-size: 54px;
    line-height: 1;
  }
  .title-rule {
    position: absolute;
    left: 8px;
    top: 76px;
    width: 685px;
    height: 3px;
    background: linear-gradient(90deg, var(--ink) 0%, var(--ink) 62%, var(--rule-soft) 75%, transparent 100%);
  }
  .dish {
    position: absolute;
    left: 8px;
    width: 670px;
  }
  .dish-name {
    margin: 0;
    font-family: "Great Vibes", cursive;
    font-weight: 400;
    font-size: 40px;
    line-height: 1;
    color: var(--ink);
  }
  .dish-desc {
    margin: 6px 0 0;
    font-family: "Gabriela", serif;
    font-size: 16.5px;
    line-height: 29px;
    white-space: pre-line;
  }
  .section-title {
    position: absolute;
    left: 16px;
    top: 736px;
    margin: 0;
    font-family: "UnifrakturCook", serif;
    font-weight: 700;
    font-size: 52px;
    line-height: 1;
  }
  .strata-list {
    position: absolute;
    left: 16px;
    top: 804px;
    margin: 0;
    padding: 0;
    list-style: none;
    font-family: "Sorts Mill Goudy", serif;
    font-size: 17px;
    line-height: 21px;
  }
</style>
</head>
<body>
  <main class="menu-page">
    <div class="food-photo" role="img" aria-label="Close-up photo of golden baked breakfast pastry over red ingredients"></div>

    <section class="content">
      <h1 class="page-title">Hearty Breakfast</h1>
      <div class="title-rule"></div>

      <article class="dish" style="top:94px">
        <h2 class="dish-name">Breakfast Croissantwich</h2>
        <p class="dish-desc">Farm-fresh Eggs and Cheese, Farm-fresh Eggs and Applewood Smoked Bacon,
Farm-Fresh Eggs and Maple Sausage, or Farm-Fresh Eggs and Scrapple.
Don’t want a Croissant? Sandwich size English Muffins, Fresh Baked Biscuits, and
Brooklyn Bagels available on request.</p>
      </article>

      <article class="dish" style="top:262px">
        <h2 class="dish-name">Chef Mateo's Breakfast Burrito</h2>
        <p class="dish-desc">Jumbo flour tortilla filled with Redskin Potatoes, Farm-fresh Eggs,
Shredded Cheddar, and your choice of meat or extra cheese.  Choose from; Chorizo
Sausage, Applewood Smoked Bacon, Maple Sausage, or Country Ham.
Served with fresh Chef made Salsa. Add avocado</p>
      </article>

      <article class="dish" style="top:444px">
        <h2 class="dish-name">Individual Quiche</h2>
        <p class="dish-desc">Spinach and Cheese, Local Tomato and Applewood Smoked Bacon,  Maple Sausage
and Redskin Potato, or Asparagus and Crab.</p>
      </article>

      <article class="dish" style="top:564px">
        <h2 class="dish-name">Farmhouse Breakfast</h2>
        <p class="dish-desc">Country Cheddar Scrambled Eggs Served with Redskin Potato Hash Browns,
Baked Spiced Apples, Fresh Baked Gourmet Muffins and Buttery Biscuits, and
Your Choice of One; Applewood Smoked Bacon, Maple Sausage Links, or Country Ham</p>
      </article>

      <h2 class="section-title">Breakfast Strata’s</h2>
      <ul class="strata-list">
        <li>Breakfast Stratas-serves 10-12 ppl</li>
        <li>French Toast Strata</li>
        <li>Redskin Potato and Maple Sausage Strata</li>
        <li>Twice Baked Breakfast Potato Casserole</li>
      </ul>
    </section>
  </main>
</body>
</html>
```